Website for International Non-Profit for Birth Parent Searching

LumaKin is a 501(c)(3) non-profit organization that helps Chinese adoptees search and reunite with birth families who were separated due the One Child Policy in China. We want to create a website that can link to an information database that allows website users to easily access information around search ads in an organized way; help connect families to professional searchers; provide resources for community support for adoptees and their families as they embark on a personal and emotional journey of finding birth family through support groups on social media and consultation/education on the searching process; and provide the opportunity for the adoptive community to give back through donations and volunteer opportunities. The final design should foster a sense of community and be easy navigable to access the multiple resources we provide to help families search for each other. We would like to see designs with red/black/white color schemes that are gentle, inviting, and family friendly to viewers. We would like to see some design layouts with Chinese themes, if possible.

```html
<!DOCTYPE html>
<html lang="en">
<head>
<meta charset="utf-8">
<title>LumaKin – Resources</title>
<link href="https://fonts.googleapis.com/css2?family=Barlow:wght@400;500;600;700&family=Lato:wght@400;700&family=Roboto:wght@400;500&display=swap" rel="stylesheet">
<style>
:root{
  --red:#a1000f;
  --red-bright:#c8121f;
  --ink:#161616;
  --text:#333;
  --panel:#f1f1f1;
  --line:#c9c9c9;
  --footer:#0d0d0d;
  --link:#1157a8;
}
*{box-sizing:border-box;margin:0;padding:0}
html,body{width:846px;height:1200px;overflow:hidden;background:#fff;font-family:"Barlow",sans-serif;color:var(--ink)}
.page{position:relative;width:846px;height:1200px}

.site-header{position:absolute;top:0;left:0;width:846px;height:63px;background:#fff;z-index:3}
.brand-badge{position:absolute;left:45px;top:-12px;width:130px;height:134px;border-radius:50%;background:#fff;display:flex;align-items:center;justify-content:center;z-index:4}
.brand-name{font-family:"Barlow",sans-serif;font-weight:700;font-size:22px;color:var(--ink);margin-top:30px}
.main-nav{position:absolute;left:214px;top:20px;display:flex;gap:19px;font-size:11px;font-weight:600;text-transform:uppercase;color:#222;line-height:18px}
.main-nav .active{color:var(--red)}
.main-nav .has-menu::after{content:"⌄";margin-left:7px;font-size:10px}
.donate-btn{position:absolute;left:652px;top:15px;width:105px;height:29px;background:var(--red);color:#fff;border-radius:2px;font-size:10px;font-weight:600;display:flex;align-items:center;justify-content:center}
.lang{position:absolute;left:771px;top:20px;font-size:11px;font-weight:600;line-height:18px}
.lang::after{content:"⌄";margin-left:8px;font-size:10px}

.hero{position:absolute;top:63px;left:0;width:846px;height:285px}

.intro{position:absolute;top:378px;left:127px;width:592px;text-align:center}
.intro h1{font-size:25px;font-weight:700;letter-spacing:.2px}
.intro p{margin-top:14px;font-family:"Lato",sans-serif;font-size:11px;line-height:17px;color:var(--text)}

.resource-panel{position:absolute;top:554px;left:102px;width:643px;height:358px;background:var(--panel)}
.resource-photo{position:absolute;left:0;top:0;width:294px;height:358px;background:linear-gradient(160deg,#ececec 0%,#e2ddd6 45%,#e39a2e 75%,#c8861f 100%)}
.resource-form{position:absolute;left:327px;top:43px;width:285px}
.select-field{height:32px;background:#fff;border:1px solid var(--line);border-radius:2px;margin-bottom:13px;padding:0 12px;display:flex;align-items:center;justify-content:space-between;font-family:"Roboto",sans-serif;font-size:10px;color:#222}
.upload-row{display:flex;align-items:center;justify-content:space-between;margin-top:-2px}
.upload-label{font-family:"Lato",sans-serif;font-size:10px;line-height:13px;color:#333}
.upload-label small{font-size:8px}
.file-box{width:212px;height:38px;background:#fff;border:1px solid var(--line);border-radius:2px;display:flex;align-items:center;padding-left:8px;gap:13px;font-family:"Roboto",sans-serif}
.file-btn{width:110px;height:26px;background:#f0f0f0;border:1px solid #e2e2e2;border-radius:2px;display:flex;align-items:center;justify-content:center;font-size:10px;color:#333}
.file-status{font-size:8.5px;color:#222}
.form-note{margin-top:13px;font-family:"Lato",sans-serif;font-size:10px;line-height:16px;color:#222}
.form-note a{color:var(--link);font-weight:700;text-decoration:none}
.submit-btn{margin-top:11px;width:282px;height:33px;background:var(--red);border-radius:2px;color:#fff;font-family:"Roboto",sans-serif;font-weight:500;font-size:11px;display:flex;align-items:center;justify-content:center}
.agree{margin-top:9px;display:flex;align-items:center;gap:7px;font-family:"Lato",sans-serif;font-size:10px;color:#222}
.agree span{width:9px;height:9px;border:1px solid #bbb;border-radius:2px;background:#fff}

.site-footer{position:absolute;top:971px;left:0;width:846px;height:229px;background:var(--footer);color:#fff;font-family:"Roboto",sans-serif}
.footer-brand{position:absolute;left:112px;top:70px;font-family:"Barlow",sans-serif;font-weight:700;font-size:24px;color:#fff}
.footer-nav{position:absolute;left:257px;top:49px;display:flex;gap:19px;font-size:9.5px;font-weight:500;text-transform:uppercase}
.footer-rule{position:absolute;left:257px;top:78px;width:478px;height:1px;background:#8a8a8a}
.contact{position:absolute;top:96px;display:flex;gap:11px;font-size:9.5px;line-height:14px}
.contact-icon{width:20px;height:20px;background:#fff;display:flex;align-items:center;justify-content:center;flex:none}
.copyright{position:absolute;left:257px;top:146px;font-size:7.5px;text-transform:uppercase;letter-spacing:.2px}
</style>
</head>
<body>
<div class="page">
  <header class="site-header">
    <div class="brand-badge"><span class="brand-name">LumaKin</span></div>
    <nav class="main-nav">
      <span>Home</span><span class="has-menu">Who We Are</span><span>Start Your Search</span><span>Get Involved</span><span class="active">Resources</span>
    </nav>
    <div class="donate-btn">DONATE NOW</div>
    <div class="lang">EN</div>
  </header>

  <svg class="hero" viewBox="0 0 846 285" role="img" aria-label="Photo of a smiling family with a young child sitting outdoors among trees">
    <defs>
      <linearGradient id="heroFill" x1="0" y1="0" x2="1" y2="0">
        <stop offset="0" stop-color="#7f8a4a"/>
        <stop offset=".35" stop-color="#a99a86"/>
        <stop offset=".6" stop-color="#8f8473"/>
        <stop offset="1" stop-color="#a3ad5a"/>
      </linearGradient>
    </defs>
    <path d="M0 0H846V198C760 245 660 270 560 262C470 255 400 218 300 222C180 226 80 240 0 260Z" fill="url(#heroFill)"/>
    <path d="M0 256C80 238 180 220 300 220C400 222 470 255 560 262C660 270 760 245 846 198L846 204C760 250 660 276 560 270C470 264 400 232 300 232C180 232 80 250 0 270Z" fill="var(--red)"/>
  </svg>

  <section class="intro">
    <h1>RESOURCES</h1>
    <p>Sed ut perspiciatis unde omnis iste natus error sit voluptatem accusantium doloremque laudantium, totam rem aperiam, eaque ipsa quae ab illo inventore veritatis et quasi architecto beatae vitae dicta sunt explicabo. Nemo enim ipsam voluptatem quia voluptas sit aspernatur aut odit aut fugit, sed quia consequuntur magni dolores eos qui ratione voluptatem sequi nesciunt. Neque porro quisquam est, qui dolorem ipsum quia dolor sit amet, consectetur, adipisci velit, sed quia non numquam eius modi tempora incidunt ut labore et dolore magnam aliquam quaerat voluptatem. Ut enim ad minima veniam, quis nostrum exercitationem ullam</p>
  </section>

  <section class="resource-panel">
    <div class="resource-photo" role="img" aria-label="Photo of a smiling woman in an orange blouse writing in a notebook"></div>
    <div class="resource-form">
      <div class="select-field">List Our Affiliates<svg width="8" height="5" viewBox="0 0 8 5"><path d="M1 1l3 3 3-3" fill="none" stroke="#222" stroke-width="1.2"/></svg></div>
      <div class="select-field">List Of Mental Health<svg width="8" height="5" viewBox="0 0 8 5"><path d="M1 1l3 3 3-3" fill="none" stroke="#222" stroke-width="1.2"/></svg></div>
      <div class="select-field">Chinese Province<svg width="8" height="5" viewBox="0 0 8 5"><path d="M1 1l3 3 3-3" fill="none" stroke="#222" stroke-width="1.2"/></svg></div>
      <div class="upload-row">
        <div class="upload-label">Upload Files<br><small>doc, pdf, jpeg</small></div>
        <div class="file-box"><div class="file-btn">Choose file</div><span class="file-status">No file chosen</span></div>
      </div>
      <p class="form-note">"If you would like to contribute to our resource library, please send all documents to <a href="#">hello@lumakin-charities.org</a>"</p>
      <div class="submit-btn">SUBMIT</div>
      <div class="agree"><span></span>I agree</div>
    </div>
  </section>

  <footer class="site-footer">
    <div class="footer-brand">LumaKin</div>
    <nav class="footer-nav"><span>Home</span><span>Who We Are</span><span>Our Services</span><span>Get Involved</span><span>Tools and Resources</span><span>Contact Us</span></nav>
    <div class="footer-rule"></div>
    <div class="contact" style="left:257px">
      <div class="contact-icon"><svg width="11" height="11" viewBox="0 0 24 24"><path d="M6.6 10.8a15 15 0 0 0 6.6 6.6l2.2-2.2c.3-.3.7-.4 1-.2 1.1.4 2.3.6 3.6.6.6 0 1 .4 1 1V20c0 .6-.4 1-1 1A17 17 0 0 1 3 4c0-.6.4-1 1-1h3.5c.6 0 1 .4 1 1 0 1.3.2 2.5.6 3.6.1.3 0 .7-.2 1z" fill="var(--red-bright)"/></svg></div>
      <div>Phone:<br>555-014-2290</div>
    </div>
    <div class="contact" style="left:376px">
      <div class="contact-icon"><svg width="10" height="12" viewBox="0 0 20 24"><path d="M10 0a8 8 0 0 0-8 8c0 6 8 16 8 16s8-10 8-16a8 8 0 0 0-8-8zm0 11a3 3 0 1 1 0-6 3 3 0 0 1 0 6z" fill="var(--red-bright)"/></svg></div>
      <div>2210 Willow Crest Road,<br>4B, Aurora, CO 80016</div>
    </div>
    <div class="contact" style="left:552px">
      <div class="contact-icon"><svg width="12" height="9" viewBox="0 0 24 18"><path d="M0 0h24v18H0z" fill="var(--red-bright)"/><path d="M1 1l11 9 11-9" fill="none" stroke="#fff" stroke-width="2"/></svg></div>
      <div>Email:<br>hello@lumakin-charities.org</div>
    </div>
    <div class="copyright">© Copyrights 2021 LumaKin &nbsp;| &nbsp; All Rights Reserved</div>
  </footer>
</div>
</body>
</html>
```